Business Card Design Project

New Business Card design for Vantroke Technology Ltd using new Logo and new Tagline for staffing company.

About us from our website - www.vantroke-example.com:

VanTroke is a leading and recognized Electronic Entertainment, Workforce Augmentation, and Project Management solutions provider with clients in Electronic Entertainment, Legal, Technology, Government and other verticals that range in size from start up organizations to Meridex 500 companies. VanTroke is certified as an 8(a) minority and woman owned enterprise, Established in 2004.

Target Market(s)

Companies in Electronic Entertainment, Legal, Government and Technology

Industry/Entity Type

Business

Requirements
Must have
• Must include in small letters the following information on back:

Established in 2004
8(a)(w)(e), Cage #7KTR9, DUNS #415260387

Front should have the following:
Pavel Orrin
Vice President
5678 Bramwick Lane
Tollerby, TB 654321
555-301-4826 X 100
555-309-1175 Fax
555-301-4826 Toll Free
name@vantroke-example.com

Our Tagline: Engage • Build • Deliver

```html
<!DOCTYPE html>
<html lang="en">
<head>
<meta charset="utf-8">
<title>VanTroke Business Card</title>
<link rel="stylesheet" href="https://fonts.googleapis.com/css2?family=Michroma&display=swap">
<style>
  :root {
    --backdrop: #3b3b3d;
    --card-grey: #666769;
    --card-white: #ffffff;
    --brand-blue: #0b5cad;
    --ink-grey: #555658;
    --ink-light: #ffffff;
  }
  * { margin: 0; padding: 0; box-sizing: border-box; }
  html, body { width: 1200px; height: 534px; overflow: hidden; }
  body {
    background: var(--backdrop);
    font-family: "Michroma", sans-serif;
    position: relative;
  }
  .card {
    position: absolute;
    top: 119px;
    width: 517px;
    height: 295px;
    overflow: hidden;
  }
  .card-back { left: 62px; background: var(--card-grey); color: var(--ink-light); }
  .card-front { left: 622px; background: var(--card-white); color: var(--ink-grey); }
  .corner { position: absolute; top: 0; }
  .card-back .corner { right: 0; }
  .card-front .corner { left: 0; }

  .wordmark {
    position: absolute;
    display: flex;
    align-items: center;
    gap: 10px;
    white-space: nowrap;
  }
  .wordmark-dot {
    width: 14px; height: 14px; border-radius: 50%;
    background: var(--brand-blue);
  }
  .card-back .wordmark {
    left: 50%; top: 148px; transform: translate(-50%, -50%);
    font-size: 40px; color: var(--ink-light);
  }
  .card-front .wordmark {
    left: 38px; top: 138px; transform: translateY(-50%);
    font-size: 22px; color: var(--ink-grey);
  }
  .credentials {
    position: absolute; left: 0; right: 0; top: 247px;
    text-align: center; text-transform: uppercase; white-space: nowrap;
  }
  .credentials .established { font-size: 11px; letter-spacing: 1px; }
  .credentials .codes { font-size: 8px; margin-top: 3px; }

  .contact {
    position: absolute; left: 247px; top: 66px;
    padding-left: 14px;
    border-left: 1.5px solid var(--brand-blue);
    height: 134px;
    text-transform: uppercase;
    white-space: nowrap;
  }
  .contact .person-name { font-size: 12px; color: var(--brand-blue); line-height: 1.1; }
  .contact .person-title { font-size: 8px; margin-top: 1px; }
  .contact .address { font-size: 8.5px; margin-top: 14px; line-height: 1.3; }
  .contact .lines { font-size: 7.5px; margin-top: 11px; line-height: 1.4; }
  .contact .label, .contact .note { color: var(--brand-blue); font-size: 6px; }
  .tagline {
    position: absolute; left: 0; right: 0; top: 256px;
    text-align: center; font-size: 14px; letter-spacing: 0.5px;
    color: var(--brand-blue); text-transform: uppercase; white-space: nowrap;
  }
</style>
</head>
<body>
  <section class="card card-back">
    <svg class="corner" width="131" height="148" viewBox="0 0 131 148">
      <polygon points="0,0 131,0 131,148" fill="var(--brand-blue)"/>
    </svg>
    <div class="wordmark"><span class="wordmark-dot"></span>VanTroke</div>
    <div class="credentials">
      <p class="established">Established in 2004</p>
      <p class="codes">8(a)(w)(e), Cage #7KTR9, DUNS #415260387</p>
    </div>
  </section>

  <section class="card card-front">
    <svg class="corner" width="136" height="151" viewBox="0 0 136 151">
      <polygon points="0,0 136,0 0,151" fill="var(--brand-blue)"/>
    </svg>
    <div class="wordmark"><span class="wordmark-dot"></span>VanTroke</div>
    <div class="contact">
      <p class="person-name">Pavel Orrin</p>
      <p class="person-title">Vice President</p>
      <p class="address">5678 Bramwick Lane, Suite 210<br>Tollerby, TB 654321</p>
      <p class="lines">
        <span class="label">Phone:</span> 555-301-4826 <span class="note">(x 205)</span><br>
        <span class="label">Phone:</span> 1-555-301-4826 <span class="note">(toll free)</span><br>
        <span class="label">Fax:</span> 555-309-1175 Fax<br>
        <span class="label">Email:</span> name@vantroke-example.com<br>
        <span class="label">Website:</span> www.vantroke-example.com
      </p>
    </div>
    <p class="tagline">Engage • Build • Deliver</p>
  </section>
</body>
</html>
```